BU naseem Polytrade Web Design

We need Simple but very Elegant Website for Our Middle East Company based in Kuwait, We are not good in describing design but we need simple but elegant and responsive to attract new market and to enable us competing in business

It Company

```html
<!DOCTYPE html>
<html lang="en">
<head>
<meta charset="utf-8">
<title>Sadeem Trade – Landing Page</title>
<link rel="stylesheet" href="https://fonts.googleapis.com/css2?family=Roboto:ital,wght@0,400;0,500;0,700;0,900;1,700&display=swap">
<style>
  :root {
    --page-bg: #ffffff;
    --site-bg: #ffffff;
    --soft-bg: #fafafa;
    --ink: #111111;
    --ink-strong: #222222;
    --ink-heading: #444444;
    --ink-muted: #666666;
    --nav-ink: #6b6b6b;
    --accent: #1c6b3c;
    --accent-dark: #163d1f;
    --hero-text: #ffffff;
  }
  * { box-sizing: border-box; margin: 0; padding: 0; }
  html, body {
    width: 1200px; height: 1200px; overflow: hidden;
    background: var(--page-bg);
    font-family: "Roboto", Arial, sans-serif;
  }
  .site {
    position: absolute; left: 0; top: 122px;
    width: 1200px; height: 956px;
    background: var(--site-bg);
    overflow: hidden;
  }
  /* Header */
  .site-header {
    position: absolute; left: 0; top: 0; width: 1200px; height: 84px;
    background: var(--site-bg);
  }
  .brand {
    position: absolute; left: 88px; top: 24px;
    display: flex; align-items: center; gap: 12px;
  }
  .brand-mark {
    width: 32px; height: 32px;
    border: 3px solid var(--ink-strong);
  }
  .brand-name {
    font-weight: 700; font-size: 27px; color: var(--ink-strong);
    letter-spacing: -0.5px; line-height: 36px;
  }
  .main-nav a {
    position: absolute; top: 34px;
    font-size: 12px; font-weight: 500; color: var(--nav-ink);
    text-decoration: none; white-space: nowrap;
  }
  .main-nav a.is-active { color: var(--ink); }
  .nav-indicator {
    position: absolute; left: 502px; top: 82px; width: 50px; height: 2px;
    background: var(--accent);
  }
  /* Hero */
  .hero {
    position: absolute; left: 0; top: 84px; width: 1200px; height: 442px;
  }
  .hero-photo {
    position: absolute; inset: 0;
    background:
      linear-gradient(180deg,
        #6f6cd0 0%, #8a86da 18%, #9d97d6 32%,
        #7a77b4 45%, #5b5d8e 60%, #4a4660 74%,
        #6a5140 86%, #3a2e2a 100%);
  }
  .hero-title {
    position: absolute; left: 0; right: 0; top: 196px;
    text-align: center; color: var(--hero-text);
    font-weight: 900; font-size: 72px; letter-spacing: -3px; line-height: 1;
  }
  .hero-tagline {
    position: absolute; left: 0; right: 0; top: 262px;
    text-align: center; color: var(--hero-text);
    font-style: italic; font-weight: 700; font-size: 23px; letter-spacing: -1px; line-height: 28px;
  }
  .hero-tagline-note {
    position: absolute; left: 0; right: 0; top: 286px;
    text-align: center; color: var(--hero-text);
    font-style: italic; font-weight: 700; font-size: 16px; letter-spacing: -0.5px; line-height: 20px;
  }
  /* Features */
  .features {
    position: absolute; left: 0; top: 526px; width: 1200px; height: 430px;
    background: linear-gradient(180deg, var(--site-bg) 0%, var(--site-bg) 26%, var(--soft-bg) 31%, var(--soft-bg) 100%);
  }
  .feature { position: absolute; top: 47px; width: 300px; }
  .feature-title {
    font-size: 16px; font-weight: 500; letter-spacing: 2px;
    color: var(--ink); margin-left: 32px; line-height: 20px;
  }
  .feature-text {
    margin-top: 14px; font-size: 12px; line-height: 15.5px; color: var(--ink);
  }
  .feature-text strong { color: var(--accent-dark); font-weight: 500; }
  .statement {
    position: absolute; left: 0; right: 0; top: 249px;
    text-align: center; font-size: 28px; font-weight: 500;
    letter-spacing: 4px; color: var(--ink-heading);
  }
  .intro {
    position: absolute; left: 0; right: 0; top: 358px;
    text-align: center; font-size: 12px; line-height: 19px; color: var(--ink-muted);
  }
</style>
</head>
<body>
  <div class="site">
    <header class="site-header">
      <div class="brand">
        <span class="brand-mark"></span>
        <span class="brand-name">Sadeem Trade</span>
      </div>
      <nav class="main-nav">
        <a class="is-active" href="#" style="left:510px">Home</a>
        <a href="#" style="left:568px">About us</a>
        <a href="#" style="left:642px">Products</a>
        <a href="#" style="left:714px">Industries</a>
        <a href="#" style="left:790px">Innovation</a>
        <a href="#" style="left:882px">Careers</a>
        <a href="#" style="left:956px">News &amp; Media</a>
      </nav>
      <span class="nav-indicator"></span>
    </header>

    <section class="hero">
      <div class="hero-photo" role="img" aria-label="City skyline at dusk with lit towers under a violet sky"></div>
      <h1 class="hero-title">Sadeem Trade</h1>
      <p class="hero-tagline">Lorem ipsum dolor sit amet</p>
      <p class="hero-tagline-note">(TAGLINE)</p>
    </section>

    <section class="features">
      <article class="feature" style="left:113px">
        <h2 class="feature-title">LOREM IPSUM</h2>
        <p class="feature-text">Lorem ipsum dolor sit amet, consectetur adipiscing<br>elit. Aenean mollis dapibus placerat.<br>Donec accumsan <strong>ultrices faucibus.</strong> Duis at ex sed.</p>
      </article>
      <article class="feature" style="left:461px">
        <h2 class="feature-title">LOREM IPSUM</h2>
        <p class="feature-text">Lorem ipsum dolor sit amet, consectetur adipiscing<br>elit. Aenean mollis dapibus placerat.<br>Donec accumsan <strong>ultrices faucibus.</strong> Duis at ex sed.</p>
      </article>
      <article class="feature" style="left:797px">
        <h2 class="feature-title">LOREM IPSUM</h2>
        <p class="feature-text">Lorem ipsum dolor sit amet, consectetur adipiscing<br>elit. Aenean mollis dapibus placerat.<br>Donec accumsan <strong>ultrices faucibus.</strong> Duis at ex sed.</p>
      </article>

      <h2 class="statement">NEQUE PORRO QUISQUAM EST QUI DOLOREM IPSUM</h2>
      <p class="intro">Lorem ipsum dolor sit amet, consectetur adipiscing elit. Mauris maximus tristique sem, ut condimentum odio aliquet vitae.<br>Nunc eu rutrum justo. Pellentesque habitant morbi tristique senectus et netus et malesuada fames ac turpis egestas.Phasellus cursus condimentum est</p>
    </section>
  </div>
</body>
</html>
```